Business card for medical clinic

I need an upmarket, modern medical/health business card for my clinic

Contact Information for Business Card

name, address, email, qr code

```html
<!DOCTYPE html>
<html lang="en">
<head>
<meta charset="utf-8">
<title>Meridian Care Clinic — Business Card</title>
<link rel="stylesheet" href="https://fonts.googleapis.com/css2?family=Montserrat:wght@400;500;700&display=swap">
<style>
  :root {
    --backdrop: #262626;
    --card-white: #ffffff;
    --card-black: #161616;
    --brand-blue: #1f7fb8;
    --accent-sky: #29abe2;
    --text-light: #f2f2f2;
  }
  * { box-sizing: border-box; margin: 0; padding: 0; }
  html, body {
    width: 1200px; height: 880px; overflow: hidden;
    background: var(--backdrop);
    font-family: "Montserrat", sans-serif;
  }
  .sheet { position: relative; width: 1200px; height: 880px; }
  .card {
    position: absolute; left: 250px; width: 700px; height: 400px;
    border-radius: 28px; overflow: hidden; background: var(--card-white);
    box-shadow: 0 14px 30px rgba(0,0,0,.45);
  }
  .card--front { top: 20px; }
  .card--back { top: 460px; }

  .brand { position: absolute; display: flex; align-items: center; gap: 14px; }
  .brand__dot { border-radius: 50%; background: var(--brand-blue); flex: none; }
  .brand__name { color: var(--brand-blue); font-weight: 700; letter-spacing: .06em; text-transform: uppercase; white-space: nowrap; }

  .card--front .brand { left: 50%; top: 50%; transform: translate(-50%, -50%); }
  .card--front .brand__dot { width: 46px; height: 46px; }
  .card--front .brand__name { font-size: 34px; }

  .card--back .brand { left: 290px; top: 50px; }
  .card--back .brand__dot { width: 26px; height: 26px; }
  .card--back .brand__name { font-size: 20px; }

  .back-divider { position: absolute; inset: 0; width: 700px; height: 400px; }

  .holder { position: absolute; left: 60px; top: 228px; }
  .holder__name { color: var(--accent-sky); font-weight: 700; font-size: 30px; letter-spacing: .02em; line-height: 36px; }
  .holder__role { color: var(--text-light); font-size: 15px; margin-top: 2px; }

  .contacts { position: absolute; left: 60px; top: 306px; list-style: none; }
  .contacts li { display: flex; align-items: center; gap: 10px; color: var(--text-light); font-size: 15px; line-height: 26px; }
  .contacts svg { width: 14px; height: 14px; fill: var(--accent-sky); flex: none; }

  .address { position: absolute; right: 50px; top: 232px; text-align: right; color: var(--text-light); font-size: 15px; line-height: 24px; }
</style>
</head>
<body>
<main class="sheet">
  <section class="card card--front" aria-label="Card front">
    <div class="brand">
      <span class="brand__dot"></span>
      <span class="brand__name">Meridian Care Clinic</span>
    </div>
  </section>

  <section class="card card--back" aria-label="Card back">
    <svg class="back-divider" viewBox="0 0 700 400" aria-hidden="true">
      <path d="M0,250 C40,195 130,172 320,168 C540,163 670,145 700,40 V400 H0 Z" fill="var(--card-black)"/>
      <path d="M0,238 C40,183 130,160 320,156 C540,151 668,133 700,28" fill="none" stroke="var(--accent-sky)" stroke-width="5"/>
    </svg>

    <div class="brand">
      <span class="brand__dot"></span>
      <span class="brand__name">Meridian Care Clinic</span>
    </div>

    <div class="holder">
      <p class="holder__name">DANIEL HART</p>
      <p class="holder__role">Managing Director</p>
    </div>

    <ul class="contacts">
      <li>
        <svg viewBox="0 0 24 24" aria-hidden="true"><path d="M6.6 10.8a15.1 15.1 0 0 0 6.6 6.6l2.2-2.2c.3-.3.7-.4 1-.2 1.1.4 2.3.6 3.6.6.6 0 1 .4 1 1V20c0 .6-.4 1-1 1A17 17 0 0 1 3 4c0-.6.4-1 1-1h3.5c.6 0 1 .4 1 1 0 1.3.2 2.5.6 3.6.1.3 0 .7-.2 1z"/></svg>
        123 456 789
      </li>
      <li>
        <svg viewBox="0 0 24 24" aria-hidden="true"><path d="M2 5h20v14H2zm2 2v.5l8 5 8-5V7l-8 5z"/></svg>
        info@yourmail.com
      </li>
      <li>
        <svg viewBox="0 0 24 24" aria-hidden="true"><circle cx="12" cy="12" r="10"/></svg>
        www.yourwebsite.com
      </li>
    </ul>

    <p class="address">Your address, City<br>State, Zip 1234</p>
  </section>
</main>
</body>
</html>
```